Fern Gate book design

I would like a new cover design to my book Fern Gate. It is a self help book for teenagers that I give away in public schools while I speak on suicide prevention type topics. I will send you the current cover that has the Fern Gate logo on it. The tag line now says, "raising the value of human life" I want to change that to, "Discovering your Real Worth."

```html
<!DOCTYPE html>
<html lang="en">
<head>
<meta charset="utf-8">
<title>Fern Gate – Book Cover</title>
<link href="https://fonts.googleapis.com/css2?family=Source+Sans+3:wght@400;600;700;800&display=swap" rel="stylesheet">
<style>
  :root {
    --backdrop: #262626;
    --red-deep: #8e0a0e;
    --red-mid: #a63a3c;
    --red-soft: #d8aeae;
    --mist: #f0eeee;
    --title-grey: #474747;
    --ink: #1f1f1f;
    --white: #ffffff;
  }
  html, body {
    margin: 0;
    padding: 0;
    width: 1200px;
    height: 1200px;
    overflow: hidden;
    background: var(--backdrop);
    font-family: "Source Sans 3", sans-serif;
  }
  .canvas {
    position: relative;
    width: 1200px;
    height: 1200px;
    background: var(--backdrop);
  }
  .cover {
    position: absolute;
    left: 248px;
    top: 56px;
    width: 704px;
    height: 1088px;
    overflow: hidden;
  }
  .cover-backdrop {
    position: absolute;
    inset: 0;
    background: linear-gradient(
      to bottom,
      var(--red-deep) 0%,
      var(--red-mid) 18%,
      var(--red-soft) 38%,
      var(--mist) 50%,
      var(--red-soft) 64%,
      var(--red-mid) 84%,
      var(--red-deep) 100%
    );
  }
  .title-block {
    position: absolute;
    left: 0;
    right: 0;
    top: 468px;
    text-align: center;
  }
  .book-title {
    margin: 0;
    font-weight: 800;
    font-size: 96px;
    line-height: 1;
    letter-spacing: 1px;
    text-transform: uppercase;
    color: var(--title-grey);
  }
  .tagline {
    margin: 14px 0 0;
    font-weight: 400;
    font-size: 19px;
    color: var(--ink);
  }
  .credits {
    position: absolute;
    left: 0;
    right: 0;
    top: 972px;
    text-align: center;
    color: var(--white);
  }
  .authors {
    margin: 0;
    font-weight: 700;
    font-size: 23px;
    line-height: 1.2;
  }
  .foreword {
    margin: 8px 0 0;
    font-weight: 600;
    font-size: 15px;
  }
</style>
</head>
<body>
  <main class="canvas">
    <section class="cover">
      <div class="cover-backdrop" role="img" aria-label="Photo of a large seated audience in an auditorium, tinted red and fading to white at the centre"></div>
      <div class="title-block">
        <h1 class="book-title">Fern Gate</h1>
        <p class="tagline">Discovering your Real Worth</p>
      </div>
      <div class="credits">
        <p class="authors">Daniel Reyes with Owen Carter</p>
        <p class="foreword">Forward by Ridgeview survivor, Lena Brooks</p>
      </div>
    </section>
  </main>
</body>
</html>
```